redesign of my existing custom website into Wordpress based website

I need someone to redesign my current website into something more classy, simplistic, modern and on trend. I would like it set up on Wordpress in a way thats easy for me to make my own additions to blogs/price changes and promotion banners. I will also need a page that is password protected so members can login and have access to all my training videos and resources.
website is www.tidewellmamas.com.au

Target Market(s)

new mums

Industry/Entity Type

Fitness

Coding

Coded - Design and coding required

Number of Pages Required

5+ page

Colors
33a6d7

Requirements
Must have
• chic, modern, stylish and simplistic.
• a call to action above the page fold
• mobile friendly conversion
• a pop up message as soon as someone enters my sight offering my free report
• a members page that is password protected containing 3 youtube videos and 6 pdf attachments as resources
• a home page
• a contact us page
• an about us page
• a blog page
• a store page
Nice to have
• some examples of my peers websites that I like:
• www.norapellwick.com
• https://www.9qlr.com
• https://41bytedgarth.com
Should not have
• anything gimmicky

```html
<!DOCTYPE html>
<html lang="en">
<head>
<meta charset="utf-8">
<title>Tidewell Mamas – Home Fitness</title>
<link href="https://fonts.googleapis.com/css2?family=Lato:wght@400;700;900&family=Open+Sans:ital,wght@0,400;0,600;0,700;1,400;1,600&display=swap" rel="stylesheet">
<style>
:root{
  --blue:#33a6d7;
  --blue-dark:#2b93c2;
  --ink:#222831;
  --text:#555b63;
  --muted:#8a9097;
  --line:#e3e7eb;
  --pale:#f3f7fb;
  --white:#ffffff;
  --brand:#c2185b;
  --foot:#ffffff;
}
*{box-sizing:border-box;margin:0;padding:0}
html,body{width:1200px;height:3922px;overflow:hidden}
body{font-family:"Open Sans",Arial,sans-serif;color:var(--text);background:var(--white);position:relative}
h1,h2,h3,h4{font-family:"Lato","Helvetica Neue",sans-serif;color:var(--ink)}
.section{position:absolute;left:0;width:1200px}
.ticks{list-style:none}
.ticks li{position:relative;padding-left:30px;font-size:13px;line-height:20px;margin-bottom:14px;color:var(--text)}
.ticks li svg{position:absolute;left:0;top:2px}

/* header */
.site-header{top:0;height:92px;background:var(--white);z-index:5}
.brand{position:absolute;left:90px;top:4px;width:184px;height:184px;border-radius:50%;background:var(--white);display:flex;align-items:center;justify-content:center;box-shadow:0 2px 6px rgba(0,0,0,.08)}
.brand span{font-family:"Lato",sans-serif;font-weight:700;font-size:22px;color:var(--brand);text-align:center;line-height:26px}
.nav{position:absolute;right:60px;top:34px;display:flex;align-items:center;gap:0}
.nav a{font-family:"Lato",sans-serif;font-size:14px;font-weight:700;color:var(--ink);text-decoration:none;margin-left:40px;text-transform:uppercase}
.nav a.active{color:var(--blue)}
.nav .cart{margin-left:34px;width:28px;height:28px;border-radius:50%;border:2px solid var(--blue);display:flex;align-items:center;justify-content:center}
.nav .login{display:flex;align-items:center;gap:6px}

/* hero */
.hero{top:92px;height:488px;background:linear-gradient(90deg,#3d4146 0%,#5d6166 45%,#8f9397 100%)}
.hero-photo{position:absolute;right:150px;top:0;width:480px;height:488px;background:radial-gradient(ellipse at 50% 40%,#c9a58e 0%,#a98670 30%,#79ab3f 60%,rgba(110,150,70,0) 80%)}
.hero-copy{position:absolute;left:98px;top:130px;width:520px}
.hero-copy h1{color:var(--white);font-size:38px;line-height:46px;font-weight:700;text-transform:uppercase;padding-bottom:18px;border-bottom:2px solid rgba(255,255,255,.7);width:510px}
.hero-copy p{color:var(--white);font-size:16px;line-height:26px;margin-top:18px;font-weight:600}
.hero-btns{display:flex;gap:22px;margin-top:28px}
.btn{display:inline-flex;align-items:center;justify-content:center;height:44px;border-radius:22px;font-family:"Lato",sans-serif;font-weight:700;font-size:14px;text-transform:uppercase;text-decoration:none}
.btn-blue{background:var(--blue);color:var(--white);width:164px;gap:8px}
.btn-ghost{border:2px solid var(--white);color:var(--white);width:164px}
.arrow{position:absolute;top:220px}

/* pillars */
.pillars{top:580px;height:400px;text-align:center}
.pillars h2{font-size:28px;font-weight:700;margin-top:58px}
.pillar-row{position:absolute;top:131px;left:98px;width:1004px;display:flex;justify-content:space-between}
.pillar{width:170px}
.circle{width:170px;height:170px;border-radius:50%;border:2px solid #d9dde1;display:flex;align-items:center;justify-content:center}
.pillar h3{font-size:18px;font-weight:700;margin-top:28px}

/* program */
.program{top:980px;height:434px;background:var(--pale)}
.program h2{position:absolute;left:96px;top:44px;font-size:30px;line-height:38px;font-weight:700;width:460px}
.program .ticks{position:absolute;left:96px;top:150px}
.program .ticks li{margin-bottom:16px}
.video{position:absolute;left:606px;top:68px;width:492px;height:293px;background:linear-gradient(135deg,#2b2f36,#4e4a55 50%,#6b5e52);}
.video-bar{position:absolute;left:0;top:0;width:100%;height:34px;background:rgba(0,0,0,.45);color:var(--white);font-size:13px;font-weight:600;padding:8px 12px}
.play{position:absolute;left:216px;top:116px;width:60px;height:60px;border-radius:50%;background:rgba(0,0,0,.55);display:flex;align-items:center;justify-content:center}

/* optin */
.optin{top:1414px;height:343px;background:var(--blue)}
.optin-copy{position:absolute;left:96px;top:40px;width:420px;color:var(--white)}
.optin-copy h2{color:var(--white);font-size:30px;line-height:38px;font-weight:700}
.optin-copy p{font-size:13px;line-height:20px;margin-top:20px}
.optin-copy em{display:block;font-family:"Open Sans",sans-serif;font-weight:600;font-size:20px;margin-top:26px}
.optin-form{position:absolute;left:557px;top:37px;width:489px;height:266px;border:3px solid var(--white);padding:26px 22px}
.field{height:44px;border:1px solid rgba(255,255,255,.85);color:var(--white);font-size:13px;padding:12px 16px;margin-bottom:14px}
.agree{display:flex;align-items:center;gap:10px;color:var(--white);font-size:13px;margin:8px 0 14px}
.agree i{width:14px;height:14px;background:var(--white);display:block}
.optin-form .submit{display:flex;height:46px;border-radius:23px;background:var(--white);color:var(--ink);font-family:"Lato",sans-serif;font-weight:700;font-size:15px;text-transform:uppercase;align-items:center;justify-content:center}

/* included */
.included{top:1757px;height:433px;background:var(--pale)}
.pack{position:absolute;left:144px;top:47px;width:405px;height:339px;background:linear-gradient(150deg,#5b3c3a 0%,#d8475f 45%,#f2f2f2 75%,#e63b8c 100%);border-radius:4px}
.included h2{position:absolute;left:651px;top:62px;font-size:30px;font-weight:700}
.included .ticks{position:absolute;left:651px;top:122px}

/* different */
.different{top:2190px;height:288px;text-align:center}
.different h2{font-size:30px;font-weight:700;margin-top:44px}
.diff-row{position:absolute;top:117px;left:90px;width:1020px;display:flex;justify-content:space-between}
.diff{width:250px}
.diff p{font-family:"Lato",sans-serif;font-size:18px;line-height:26px;color:var(--ink);margin-top:18px}

/* equipment */
.equipment{top:2478px;height:397px;background:linear-gradient(90deg,#f0f0f1 0%,#e7e6e8 50%,#d8d3d4 100%)}
.equipment-photo{position:absolute;right:0;top:0;width:600px;height:397px;background:linear-gradient(180deg,#ebe8e8 0%,#ddd6d3 55%,#b9a9b8 86%,#9d8ba1 100%)}
.equipment h2{position:absolute;left:96px;top:54px;font-size:30px;font-weight:700}
.equipment .ticks{position:absolute;left:96px;top:125px}

/* news */
.news{top:2875px;height:523px;text-align:center}
.news h2{font-size:30px;font-weight:700;margin-top:52px}
.cards{position:absolute;top:113px;left:97px;width:1011px;display:flex;justify-content:space-between;text-align:left}
.card{width:320px}
.card-img{height:206px;position:relative}
.date{position:absolute;left:0;bottom:-22px;width:52px;height:60px;background:var(--blue);color:var(--white);text-align:center;font-family:"Lato",sans-serif}
.date b{display:block;font-size:22px;margin-top:8px}
.date small{font-size:11px;text-transform:uppercase}
.card h3{font-size:18px;font-weight:700;margin-top:40px}
.card p{font-size:12px;line-height:20px;margin-top:10px;height:40px}
.meta{display:flex;gap:22px;font-size:12px;color:var(--muted);border-top:1px solid var(--line);margin-top:20px;padding-top:14px}
.meta span{display:flex;align-items:center;gap:6px}

/* testimonial */
.testimonial{top:3398px;height:217px;background:var(--blue)}
.avatar{position:absolute;left:113px;top:47px;width:124px;height:124px;border-radius:50%;border:4px solid var(--white);background:linear-gradient(160deg,#c9b8a8,#7d6d62)}
.quote{position:absolute;left:270px;top:42px;width:840px;border-left:2px solid rgba(255,255,255,.6);padding-left:28px;color:var(--white)}
.quote p{font-style:italic;font-size:14px;line-height:26px}
.quote cite{display:block;font-style:normal;font-family:"Lato",sans-serif;font-size:18px;font-weight:700;margin-top:14px}

/* footer */
.site-footer{top:3615px;height:228px;background:var(--foot)}
.foot-brand{position:absolute;left:96px;top:50px;width:200px;height:130px;display:flex;align-items:center;gap:12px}
.foot-brand i{width:44px;height:44px;border-radius:50%;border:3px solid var(--brand);display:block;flex:none}
.foot-brand span{font-family:"Lato",sans-serif;font-weight:700;font-size:22px;color:var(--brand);line-height:26px}
.foot-col{position:absolute;top:42px}
.foot-col h4{font-size:18px;font-weight:700;margin-bottom:14px}
.foot-col a{display:block;font-size:12px;line-height:19px;color:var(--text);text-decoration:none}
.foot-col p{font-size:12px;line-height:19px}
.email-field{width:252px;height:38px;border-bottom:1px solid var(--line);font-size:12px;color:var(--muted);padding:12px 4px;margin-top:10px}
.subscribe{display:inline-block;margin-top:14px;border:1px solid var(--blue);color:var(--blue);font-size:11px;font-weight:700;padding:6px 12px;text-transform:uppercase}
.contact-line{display:flex;gap:12px;align-items:flex-start;font-size:12px;line-height:18px;margin-bottom:18px}
.bottom-bar{top:3843px;height:79px;border-top:1px solid var(--line);margin:0 96px;width:1008px;left:0}
.bottom-bar p{position:absolute;left:0;top:28px;font-size:12px}
.socials{position:absolute;right:44px;top:24px;display:flex;gap:10px}
.socials i{width:24px;height:24px;border-radius:50%;background:var(--blue);display:block}
.code{position:absolute;right:0;top:28px;font-size:12px}
</style>
</head>
<body>

<header class="section site-header">
  <div class="brand"><span>Tidewell<br>Mamas</span></div>
  <nav class="nav">
    <a class="active">Home</a><a>About Us</a><a>Program</a><a>Blog</a><a>Shop</a><a>Contact Us</a>
    <span class="cart"><svg width="14" height="14" viewBox="0 0 24 24" fill="none" stroke="#33a6d7" stroke-width="2.5"><path d="M2 3h3l3 12h11l3-8H7"/><circle cx="9" cy="20" r="1.6"/><circle cx="18" cy="20" r="1.6"/></svg></span>
    <a class="login"><svg width="12" height="14" viewBox="0 0 12 14"><rect x="1" y="6" width="10" height="8" rx="1" fill="#33a6d7"/><path d="M3 6V4a3 3 0 0 1 6 0v2" fill="none" stroke="#33a6d7" stroke-width="1.8"/></svg>Login</a>
  </nav>
</header>

<section class="section hero">
  <div class="hero-photo" role="img" aria-label="Smiling fitness trainer in a green workout top"></div>
  <svg class="arrow" style="left:34px" width="24" height="40" viewBox="0 0 24 40"><path d="M20 4 4 20l16 16" fill="none" stroke="#fff" stroke-width="4"/></svg>
  <svg class="arrow" style="right:34px" width="24" height="40" viewBox="0 0 24 40"><path d="M4 4l16 16L4 36" fill="none" stroke="#fff" stroke-width="4"/></svg>
  <div class="hero-copy">
    <h1>12 Week Home Workout Program for Mums!</h1>
    <p>Your purchase of the Home Workout Program - Equipment Pack comes loaded with value</p>
    <div class="hero-btns">
      <a class="btn btn-blue">Watch Now <svg width="14" height="14" viewBox="0 0 14 14"><circle cx="7" cy="7" r="7" fill="#fff"/><path d="M5.5 4v6l4.5-3z" fill="#33a6d7"/></svg></a>
      <a class="btn btn-ghost">Join Now</a>
    </div>
  </div>
</section>

<section class="section pillars">
  <h2>Lose your baby weight and get back into great shape!</h2>
  <div class="pillar-row">
    <div class="pillar"><div class="circle"><svg width="80" height="80" viewBox="0 0 80 80" fill="none" stroke="#33a6d7" stroke-width="3"><circle cx="40" cy="26" r="10"/><path d="M22 66c0-14 8-22 18-22s18 8 18 22z" fill="#33a6d7"/><circle cx="16" cy="20" r="3"/><circle cx="64" cy="20" r="3"/><circle cx="40" cy="6" r="3"/><circle cx="14" cy="44" r="3"/><circle cx="66" cy="44" r="3"/></svg></div><h3>Mindfulness</h3></div>
    <div class="pillar"><div class="circle"><svg width="74" height="74" viewBox="0 0 74 74"><path d="M37 20c-8-6-26-4-26 16 0 18 14 32 22 30 3-1 5-1 8 0 8 2 22-12 22-30 0-20-18-22-26-16z" fill="#33a6d7"/><path d="M37 20c0-8 4-14 10-16" fill="none" stroke="#33a6d7" stroke-width="3"/><path d="M26 42l8 8 14-16" fill="none" stroke="#fff" stroke-width="4"/></svg></div><h3>Nutrition</h3></div>
    <div class="pillar"><div class="circle"><svg width="96" height="80" viewBox="0 0 96 80" fill="none" stroke="#33a6d7" stroke-width="3"><circle cx="40" cy="14" r="6" fill="#33a6d7"/><path d="M40 22l-4 22 18 4 24-32"/><path d="M36 44 20 70M54 48l4 22"/><path d="M10 74h76" stroke-width="4"/></svg></div><h3>Workout</h3></div>
    <div class="pillar"><div class="circle"><svg width="76" height="76" viewBox="0 0 76 76"><rect x="8" y="32" width="14" height="34" fill="#33a6d7"/><path d="M28 34l12-24c6 0 8 4 7 10l-3 10h20c4 0 6 4 5 8l-6 22c-1 4-4 6-8 6H28z" fill="#33a6d7"/></svg></div><h3>Motivation</h3></div>
  </div>
</section>

<section class="section program">
  <h2>12 week Home Workout Program For Mums!</h2>
  <ul class="ticks">
    <li><svg width="14" height="14" viewBox="0 0 14 14"><circle cx="7" cy="7" r="7" fill="#33a6d7"/><path d="M4 7l2 2 4-4" stroke="#fff" stroke-width="1.8" fill="none"/></svg>12 week, cardio and resistance circuit training program</li>
    <li><svg width="14" height="14" viewBox="0 0 14 14"><circle cx="7" cy="7" r="7" fill="#33a6d7"/><path d="M4 7l2 2 4-4" stroke="#fff" stroke-width="1.8" fill="none"/></svg>Triple workout DVD</li>
    <li><svg width="14" height="14" viewBox="0 0 14 14"><circle cx="7" cy="7" r="7" fill="#33a6d7"/><path d="M4 7l2 2 4-4" stroke="#fff" stroke-width="1.8" fill="none"/></svg>Workout equipment delivered to your front door</li>
    <li><svg width="14" height="14" viewBox="0 0 14 14"><circle cx="7" cy="7" r="7" fill="#33a6d7"/><path d="M4 7l2 2 4-4" stroke="#fff" stroke-width="1.8" fill="none"/></svg>Weekly coaching emails</li>
    <li><svg width="14" height="14" viewBox="0 0 14 14"><circle cx="7" cy="7" r="7" fill="#33a6d7"/><path d="M4 7l2 2 4-4" stroke="#fff" stroke-width="1.8" fill="none"/></svg>Accountability charts &amp; program cards</li>
    <li><svg width="14" height="14" viewBox="0 0 14 14"><circle cx="7" cy="7" r="7" fill="#33a6d7"/><path d="M4 7l2 2 4-4" stroke="#fff" stroke-width="1.8" fill="none"/></svg>Family friendly healthy recipes</li>
    <li><svg width="14" height="14" viewBox="0 0 14 14"><circle cx="7" cy="7" r="7" fill="#33a6d7"/><path d="M4 7l2 2 4-4" stroke="#fff" stroke-width="1.8" fill="none"/></svg>Healthy eating guidelines</li>
  </ul>
  <div class="video" role="img" aria-label="Video still of a mum exercising on a step platform with her baby on a lounge room floor">
    <div class="video-bar">Lose your baby weight and get back into great shape!</div>
    <div class="play"><svg width="22" height="24" viewBox="0 0 22 24"><path d="M2 2v20l18-10z" fill="#fff"/></svg></div>
  </div>
</section>

<section class="section optin">
  <div class="optin-copy">
    <h2>Get your<br>FREE top 10<br>Baby Belly Blasting Tips</h2>
    <p>See our secret tips to a flatter yummy mummy tummy<br>that you can start implementing</p>
    <em>for free today!</em>
  </div>
  <div class="optin-form">
    <div class="field">Name :</div>
    <div class="field">Email :</div>
    <div class="agree"><i></i>I agree to Terms &amp; Conditions</div>
    <div class="submit">Get it free now!</div>
  </div>
</section>

<section class="section included">
  <div class="pack" role="img" aria-label="Program pack with workout DVD, program cards and healthy eating guide booklet"></div>
  <h2>What's included in the program?</h2>
  <ul class="ticks">
    <li><svg width="14" height="14" viewBox="0 0 14 14"><circle cx="7" cy="7" r="7" fill="#33a6d7"/><path d="M4 7l2 2 4-4" stroke="#fff" stroke-width="1.8" fill="none"/></svg>Our unique 3 stage, 12 week training program</li>
    <li><svg width="14" height="14" viewBox="0 0 14 14"><circle cx="7" cy="7" r="7" fill="#33a6d7"/><path d="M4 7l2 2 4-4" stroke="#fff" stroke-width="1.8" fill="none"/></svg>Full Instructional Workout DVD and program cards for each program</li>
    <li><svg width="14" height="14" viewBox="0 0 14 14"><circle cx="7" cy="7" r="7" fill="#33a6d7"/><path d="M4 7l2 2 4-4" stroke="#fff" stroke-width="1.8" fill="none"/></svg>Weekly accountability charts</li>
    <li><svg width="14" height="14" viewBox="0 0 14 14"><circle cx="7" cy="7" r="7" fill="#33a6d7"/><path d="M4 7l2 2 4-4" stroke="#fff" stroke-width="1.8" fill="none"/></svg>Weekly coaching emails</li>
    <li><svg width="14" height="14" viewBox="0 0 14 14"><circle cx="7" cy="7" r="7" fill="#33a6d7"/><path d="M4 7l2 2 4-4" stroke="#fff" stroke-width="1.8" fill="none"/></svg>Funky exercise equipment for your home</li>
    <li><svg width="14" height="14" viewBox="0 0 14 14"><circle cx="7" cy="7" r="7" fill="#33a6d7"/><path d="M4 7l2 2 4-4" stroke="#fff" stroke-width="1.8" fill="none"/></svg>Nutritionist approved healthy eating guide</li>
    <li><svg width="14" height="14" viewBox="0 0 14 14"><circle cx="7" cy="7" r="7" fill="#33a6d7"/><path d="M4 7l2 2 4-4" stroke="#fff" stroke-width="1.8" fill="none"/></svg>Healthy Family Favourites recipe ebook</li>
  </ul>
</section>

<section class="section different">
  <h2>Why our program is different</h2>
  <div class="diff-row">
    <div class="diff"><svg width="64" height="56" viewBox="0 0 64 56" fill="none" stroke="#33a6d7" stroke-width="4"><rect x="6" y="12" width="40" height="40" rx="4"/><path d="M24 36l4-10 22-22 6 6-22 22z" fill="#33a6d7"/></svg><p>Specially designed for<br>Mums</p></div>
    <div class="diff"><svg width="80" height="56" viewBox="0 0 80 56" fill="#33a6d7"><rect x="4" y="22" width="6" height="12"/><rect x="12" y="12" width="8" height="32"/><rect x="22" y="26" width="36" height="4"/><rect x="60" y="12" width="8" height="32"/><rect x="70" y="22" width="6" height="12"/></svg><p>Workout equipment included<br>so you can train from home</p></div>
    <div class="diff"><svg width="70" height="56" viewBox="0 0 70 56"><circle cx="22" cy="20" r="8" fill="#33a6d7"/><circle cx="36" cy="14" r="8" fill="#33a6d7"/><circle cx="50" cy="20" r="8" fill="#33a6d7"/><path d="M6 28h58c0 14-12 24-29 24S6 42 6 28z" fill="#33a6d7"/></svg><p>Delicious low fat family<br>friendly recipes</p></div>
    <div class="diff"><svg width="64" height="56" viewBox="0 0 64 56"><rect x="22" y="4" width="20" height="10" rx="2" fill="none" stroke="#33a6d7" stroke-width="4"/><rect x="4" y="12" width="56" height="40" rx="4" fill="#33a6d7"/><path d="M28 22h8v8h8v8h-8v8h-8v-8h-8v-8h8z" fill="#fff"/></svg><p>Caters for mums at all stages<br>of post baby recovery</p></div>
  </div>
</section>

<section class="section equipment">
  <div class="equipment-photo" role="img" aria-label="Mum kneeling on a mat with dumbbells while her baby plays beside her"></div>
  <h2>Already have the equipment you need?</h2>
  <ul class="ticks">
    <li><svg width="14" height="14" viewBox="0 0 14 14"><circle cx="7" cy="7" r="7" fill="#33a6d7"/><path d="M4 7l2 2 4-4" stroke="#fff" stroke-width="1.8" fill="none"/></svg>Our 3 stage, 12 week training program</li>
    <li><svg width="14" height="14" viewBox="0 0 14 14"><circle cx="7" cy="7" r="7" fill="#33a6d7"/><path d="M4 7l2 2 4-4" stroke="#fff" stroke-width="1.8" fill="none"/></svg>Full Instructional Workout DVD for each program</li>
    <li><svg width="14" height="14" viewBox="0 0 14 14"><circle cx="7" cy="7" r="7" fill="#33a6d7"/><path d="M4 7l2 2 4-4" stroke="#fff" stroke-width="1.8" fill="none"/></svg>Weekly accountability charts</li>
    <li><svg width="14" height="14" viewBox="0 0 14 14"><circle cx="7" cy="7" r="7" fill="#33a6d7"/><path d="M4 7l2 2 4-4" stroke="#fff" stroke-width="1.8" fill="none"/></svg>Weekly coaching emails</li>
    <li><svg width="14" height="14" viewBox="0 0 14 14"><circle cx="7" cy="7" r="7" fill="#33a6d7"/><path d="M4 7l2 2 4-4" stroke="#fff" stroke-width="1.8" fill="none"/></svg>Nutritionist approved healthy eating guidelines</li>
    <li><svg width="14" height="14" viewBox="0 0 14 14"><circle cx="7" cy="7" r="7" fill="#33a6d7"/><path d="M4 7l2 2 4-4" stroke="#fff" stroke-width="1.8" fill="none"/></svg>Healthy Family Favourites recipe ebook</li>
  </ul>
</section>

<section class="section news">
  <h2>Top News</h2>
  <div class="cards">
    <article class="card">
      <div class="card-img" role="img" aria-label="Baby standing at a workout step on a lounge room rug" style="background:linear-gradient(135deg,#6b4a3e,#b56f8c 50%,#d8c8c0)"><div class="date"><b>23</b><small>Sep</small></div></div>
      <h3>The benefits of training in the morning</h3>
      <p>So it has been a while, life has been busy for me the past few months as I welcomed...</p>
      <div class="meta"><span><svg width="10" height="11" viewBox="0 0 10 11" fill="#8a9097"><circle cx="5" cy="3" r="3"/><path d="M0 11c0-3 2-5 5-5s5 2 5 5z"/></svg>Dana Ferrow</span><span><svg width="12" height="11" viewBox="0 0 12 11" fill="none" stroke="#33a6d7" stroke-width="1.5"><path d="M1 1h10v7H5l-3 2V8H1z"/></svg>3 Comments</span></div>
    </article>
    <article class="card">
      <div class="card-img" role="img" aria-label="Bowl of creamy pumpkin soup with herbs" style="background:radial-gradient(circle at 50% 55%,#d08a2a 0%,#c27a22 30%,#f2efe9 46%,#8a7a6e 80%)"><div class="date"><b>23</b><small>Sep</small></div></div>
      <h3>Creamy Pumpkin Soup</h3>
      <p>I made this for lunch the other day and it was so creamy and delicious, plus super healthy!</p>
      <div class="meta"><span><svg width="10" height="11" viewBox="0 0 10 11" fill="#8a9097"><circle cx="5" cy="3" r="3"/><path d="M0 11c0-3 2-5 5-5s5 2 5 5z"/></svg>Dana Ferrow</span><span><svg width="12" height="11" viewBox="0 0 12 11" fill="none" stroke="#33a6d7" stroke-width="1.5"><path d="M1 1h10v7H5l-3 2V8H1z"/></svg>3 Comments</span></div>
    </article>
    <article class="card">
      <div class="card-img" role="img" aria-label="Mum doing a floor exercise in the lounge room with her baby" style="background:linear-gradient(135deg,#5a4b4a,#c85a78 45%,#8d7b72)"><div class="date"><b>23</b><small>Sep</small></div></div>
      <h3>Odette's 10 exercise lounge room..</h3>
      <p>Half the battle when trying to keep fit as a mum is your ability to be able to get out of the house!</p>
      <div class="meta"><span><svg width="10" height="11" viewBox="0 0 10 11" fill="#8a9097"><circle cx="5" cy="3" r="3"/><path d="M0 11c0-3 2-5 5-5s5 2 5 5z"/></svg>Dana Ferrow</span><span><svg width="12" height="11" viewBox="0 0 12 11" fill="none" stroke="#33a6d7" stroke-width="1.5"><path d="M1 1h10v7H5l-3 2V8H1z"/></svg>3 Comments</span></div>
    </article>
  </div>
</section>

<section class="section testimonial">
  <svg class="arrow" style="left:34px;top:88px" width="20" height="36" viewBox="0 0 20 36"><path d="M17 3 3 18l14 15" fill="none" stroke="#fff" stroke-width="3" opacity=".7"/></svg>
  <svg class="arrow" style="right:34px;top:88px" width="20" height="36" viewBox="0 0 20 36"><path d="M3 3l14 15L3 33" fill="none" stroke="#fff" stroke-width="3" opacity=".7"/></svg>
  <div class="avatar" role="img" aria-label="Portrait of a program member"></div>
  <blockquote class="quote">
    <p>The program fitted around nap times and school runs so easily. I never needed a gym, the equipment came straight to my door, and the weekly emails kept me going on the hard days. Twelve weeks later I feel stronger, happier and more like myself again than I have in years.</p>
    <cite>- Mirela Tostvik</cite>
  </blockquote>
</section>

<footer class="section site-footer">
  <div class="foot-brand"><i></i><span>Tidewell<br>Mamas</span></div>
  <div class="foot-col" style="left:380px"><h4>Information</h4><a>Home</a><a>About Us</a><a>Program</a><a>Blog</a><a>Shop</a><a>Contact Us</a></div>
  <div class="foot-col" style="left:563px;width:270px"><h4>Newsletter Subscription</h4><p>Register your Email Address to get information about us</p><div class="email-field">Email Address</div><span class="subscribe">Subscribe</span></div>
  <div class="foot-col" style="left:891px;width:220px"><h4>Contact Us</h4>
    <div class="contact-line"><svg width="12" height="16" viewBox="0 0 12 16"><path d="M6 0a6 6 0 0 1 6 6c0 4-6 10-6 10S0 10 0 6a6 6 0 0 1 6-6z" fill="#33a6d7"/><circle cx="6" cy="6" r="2" fill="#fff"/></svg><span>14 Harbourline Road,<br>Kelsey Bay QLD 4870</span></div>
    <div class="contact-line"><svg width="14" height="14" viewBox="0 0 14 14"><path d="M3 1l3 3-2 2c1 2 2 3 4 4l2-2 3 3-2 2C6 13 1 8 1 3z" fill="#33a6d7"/></svg><span>+61 7 5550 1472</span></div>
    <div class="contact-line"><svg width="14" height="11" viewBox="0 0 14 11"><rect width="14" height="11" fill="#33a6d7"/><path d="M0 0l7 6 7-6" fill="none" stroke="#fff" stroke-width="1.3"/></svg><span>hello@tidewellmamas.com.au</span></div>
  </div>
</footer>
<div class="section bottom-bar">
  <p>Copyright © 2017, Tidewell Mamas. All rights reserved</p>
  <div class="socials"><i></i><i></i><i></i><i></i></div>
  <span class="code">C17</span>
</div>

</body>
</html>
```